Dunmore Roofing

Want a professional looking business card

Industry/Entity Type

Business

Contact Information for Business Card

Paul Dunmore ( Owner) paul@dunmoreroofing-example.com, www.dunmoreroofing-example.com, Adress: 4172 Township road 43 Plantagenet,ON K9X4T2

```html
<!DOCTYPE html>
<html lang="en">
<head>
<meta charset="utf-8">
<title>Dunmore Roofing — Business Card</title>
<link rel="stylesheet" href="https://fonts.googleapis.com/css2?family=Arimo:wght@400;700&display=swap">
<style>
  :root {
    --page-bg: #e6e4e2;
    --card-front: #77787a;
    --card-back: #ffffff;
    --brand-blue: #1d4289;
    --brand-grey: #8a8b8d;
    --text-grey: #6d6e70;
    --rule-grey: #d3d3d3;
    --white: #ffffff;
  }
  * { box-sizing: border-box; margin: 0; padding: 0; }
  html, body {
    width: 1200px; height: 997px; overflow: hidden;
    background: var(--page-bg);
    font-family: "Arimo", Arial, sans-serif;
  }
  .card {
    position: absolute;
    width: 525px; height: 300px;
    box-shadow: 0 6px 18px rgba(0,0,0,0.18);
    overflow: hidden;
  }
  /* Front */
  .card-front { left: 337px; top: 120px; background: var(--card-front); }
  .card-front .wordmark {
    position: absolute; left: 0; right: 0; top: 112px;
    display: flex; justify-content: center; align-items: center; gap: 12px;
    color: var(--white);
    font-weight: 700; font-size: 34px; letter-spacing: 2px; text-transform: uppercase;
  }
  .card-front .wordmark .dot {
    width: 16px; height: 16px; border-radius: 50%; background: var(--white);
  }
  .card-front .web {
    position: absolute; left: 0; right: 0; top: 224px;
    text-align: center; color: var(--white);
    font-size: 13px; letter-spacing: 1px;
  }
  /* Back */
  .card-back { left: 337px; top: 560px; background: var(--card-back); }
  .card-back .wordmark {
    position: absolute; left: 28px; top: 118px; width: 230px;
    color: var(--brand-blue);
    font-weight: 700; font-size: 24px; letter-spacing: 1px; text-transform: uppercase;
    text-align: center; line-height: 28px;
  }
  .card-back .divider {
    position: absolute; left: 278px; top: 42px; width: 1px; height: 150px;
    background: var(--rule-grey);
  }
  .contact {
    position: absolute; left: 294px; top: 44px;
    font-size: 11.5px; line-height: 15px; color: var(--text-grey);
  }
  .contact .name { color: var(--brand-blue); font-weight: 700; font-size: 13px; }
  .contact .company { color: var(--brand-blue); margin-top: 4px; }
  .contact .line { display: flex; align-items: center; gap: 6px; margin-top: 3px; }
  .contact .line.first { margin-top: 8px; }
  .contact .icon { width: 12px; height: 12px; flex: none; }
  .stripes { position: absolute; left: 0; top: 0; }
  .card-back .web {
    position: absolute; left: 24px; top: 270px;
    color: var(--white); font-size: 13px; letter-spacing: 1.5px;
  }
</style>
</head>
<body>

  <section class="card card-front" aria-label="Business card front">
    <div class="wordmark"><span class="dot"></span>Dunmore Roofing</div>
    <div class="web">www.dunmoreroofing-example.com</div>
  </section>

  <section class="card card-back" aria-label="Business card back">
    <svg class="stripes" width="525" height="300" viewBox="0 0 525 300" aria-hidden="true">
      <polygon points="0,256 298,256 320,234 525,234 525,244 326,244 326,300 0,300" fill="var(--brand-blue)"/>
      <polygon points="334,218 525,218 525,228 326,228" fill="var(--brand-grey)"/>
    </svg>

    <div class="wordmark">Dunmore<br>Roofing</div>
    <div class="divider"></div>

    <div class="contact">
      <div class="name">Paul Dunmore</div>
      <div class="role">Owner</div>
      <div class="company">Dunmore Roofing</div>
      <div>4172 Township road 43,</div>
      <div>Elmsworth Falls, NB K9X4T2</div>
      <div class="line first">
        <svg class="icon" viewBox="0 0 12 12" aria-hidden="true">
          <circle cx="6" cy="6" r="6" fill="var(--brand-blue)"/>
          <path d="M4 3.2 L5 3 L5.6 4.6 L4.9 5.1 Q5.5 6.5 6.9 7.1 L7.4 6.4 L9 7 L8.8 8 Q6.5 8.6 4.6 6.8 Q3.1 5 4 3.2Z" fill="var(--white)"/>
        </svg>
        <span>(555) 010-4872</span>
      </div>
      <div class="line">
        <svg class="icon" viewBox="0 0 12 12" aria-hidden="true">
          <circle cx="6" cy="6" r="6" fill="var(--brand-blue)"/>
          <rect x="3" y="4" width="6" height="4.2" fill="var(--white)"/>
          <path d="M3 4 L6 6.4 L9 4" stroke="var(--brand-blue)" stroke-width="0.8" fill="none"/>
        </svg>
        <span>paul@dunmoreroofing-example.com</span>
      </div>
    </div>

    <div class="web">www.dunmoreroofing-example.com</div>
  </section>

</body>
</html>
```